Powerpoint template and intro presentation

I have a short presentation of 6 slides that I'd like to be made pretty, see attached below - called target companies Intro.

I'd also like a template incorporating my logo which I have attached below as well

I've attached a jpeg with the logo with white background that is the logo that I would like to incorporate.

Powerpoint and logo file has been uploaded

```html
<!DOCTYPE html>
<html lang="en">
<head>
<meta charset="utf-8">
<title>Unified Sky Systems – Target Company Introduction Brief</title>
<link href="https://fonts.googleapis.com/css2?family=Questrial&display=swap" rel="stylesheet">
<style>
:root{
  --page:#efebe5;
  --slide:#ffffff;
  --green:#7dbb2e;
  --green-soft:#cfe3b3;
  --grey-text:#4a4a4a;
  --grey-light:#9a9a9a;
  --rule-grey:#d8d8d8;
}
*{margin:0;padding:0;box-sizing:border-box}
html,body{width:1200px;height:1000px;overflow:hidden}
body{background:var(--page);font-family:"Questrial",sans-serif;color:var(--grey-text);position:relative}
.slide{position:absolute;background:var(--slide);box-shadow:0 2px 6px rgba(0,0,0,.18);overflow:hidden}
.slide--cover{left:33px;top:68px;width:562px;height:422px}
.slide--intro{left:609px;top:70px;width:559px;height:420px}
.slide--growth{left:33px;top:507px;width:560px;height:418px}
.slide--profile{left:609px;top:507px;width:559px;height:418px}

.cover-name{position:absolute;left:0;right:0;top:178px;text-align:center;color:var(--green)}
.cover-name__main{display:block;font-size:54px;letter-spacing:1px;line-height:1}
.cover-name__sub{display:block;font-size:22px;letter-spacing:17px;margin-top:18px;line-height:1;padding-left:17px}
.cover-band{position:absolute;left:0;right:0;top:312px;height:5px;background:var(--green-soft)}
.cover-subtitle{position:absolute;left:0;right:0;top:324px;text-align:center;font-size:19px;color:var(--grey-light)}
.cover-rule{position:absolute;left:0;right:0;top:354px;height:1px;background:var(--rule-grey)}

.slide-title{position:absolute;left:0;right:0;top:28px;text-align:center;font-size:21px;color:var(--green)}
.title-rule{position:absolute;left:32px;right:40px;top:58px;height:6px;border-top:2px solid var(--green-soft);border-bottom:2px solid var(--green-soft)}

.bullets{position:absolute;list-style:none}
.bullets li{position:relative;padding-left:22px;line-height:1.15}
.bullets li::before{content:"";position:absolute;left:2px;top:8px;width:4px;height:4px;border-radius:50%;background:var(--green)}
.bullets--intro{left:30px;top:80px;width:490px;font-size:16.5px}
.bullets--intro li{margin-bottom:21px}
.bullets--growth{left:30px;top:78px;width:440px;font-size:15px}
.bullets--growth li{margin-bottom:17px}
.bullets--growth li::before{width:8px;height:6px;top:6px;border-radius:4px}
.bullets--profile{left:28px;top:85px;width:330px;font-size:14.5px}
.bullets--profile li{margin-bottom:17px}

.growth-visual{position:absolute;left:322px;top:118px;width:238px;height:262px;background:radial-gradient(ellipse at 55% 75%,#cfcfcf 0%,#e6e6e6 40%,rgba(255,255,255,0) 72%)}
.profile-photo{position:absolute;left:371px;top:91px;width:147px;height:247px;background:linear-gradient(160deg,#d9d9d9,#6e6e6e);border:1px solid #cfcfcf}

.footer-name{position:absolute;left:22px;bottom:22px;font-size:8px;color:var(--green);line-height:1.1;width:64px;text-align:center}
.footer-rule{position:absolute;left:88px;right:44px;bottom:36px;height:4px;border-top:1px solid var(--green-soft);border-bottom:2px solid var(--green-soft)}
.page-number{position:absolute;right:40px;bottom:22px;width:26px;height:18px;border-radius:9px;background:var(--green);color:#fff;font-size:8px;text-align:center;line-height:19px}
</style>
</head>
<body>

<section class="slide slide--cover">
  <div class="cover-name"><span class="cover-name__main">UNIFIED</span><span class="cover-name__sub">SKY SYSTEMS</span></div>
  <div class="cover-band"></div>
  <p class="cover-subtitle">Target Company Introduction Brief</p>
  <div class="cover-rule"></div>
</section>

<section class="slide slide--intro">
  <h2 class="slide-title">Unified Sky Systems</h2>
  <div class="title-rule"></div>
  <ul class="bullets bullets--intro">
    <li>Working with private equity funds to find Australian based cloud companies to invest in.</li>
    <li>Looking to partner with thought leaders and innovators to create a competitive cloud offering.</li>
    <li>Want to work with existing management to grow the business.</li>
    <li>We believe that market is ready for consolidation</li>
    <li>We are committed to building a large and successful Australian owned cloud services business.</li>
  </ul>
  <div class="footer-name">UNIFIED<br>SKY SYSTEMS</div>
  <div class="footer-rule"></div>
  <div class="page-number">2</div>
</section>

<section class="slide slide--growth">
  <h2 class="slide-title">Unified Sky Systems</h2>
  <div class="title-rule"></div>
  <div class="growth-visual" role="img" aria-label="Young plant growing from a pile of coins, greyscale"></div>
  <ul class="bullets bullets--growth">
    <li>Working with private equity funds to find Australian based cloud companies to invest in.</li>
    <li style="width:340px">Looking to partner with thought leaders and innovators to create a competitive cloud offering.</li>
    <li style="width:320px">Want to work with existing management to grow the business.</li>
    <li>We believe that market is ready for consolidation</li>
    <li style="width:320px">We are committed to building a large and successful Australian owned cloud services business.</li>
  </ul>
  <div class="footer-name">UNIFIED<br>SKY SYSTEMS</div>
  <div class="footer-rule"></div>
  <div class="page-number">3</div>
</section>

<section class="slide slide--profile">
  <h2 class="slide-title">Alan Marsh</h2>
  <div class="title-rule"></div>
  <ul class="bullets bullets--profile">
    <li>One of the main shareholders of Meridian Networks Australia (formerly NetCore Communications).</li>
    <li>Oversaw NetCore from a small distribution company to the leading IT operations in Australia and New Zealand employing in excess of 1200 employees.</li>
    <li>Moved NetCore from a minority private equity holding to a successful sale to Meridian Networks for a final valuation of over a Billion dollars.</li>
    <li>A member of the Meridian Networks Advisory.</li>
  </ul>
  <div class="profile-photo" role="img" aria-label="Black and white portrait photograph of Alan Marsh"></div>
  <div class="footer-name">UNIFIED<br>SKY SYSTEMS</div>
  <div class="footer-rule"></div>
  <div class="page-number">4</div>
</section>

</body>
</html>
```